Clear Harbor Business card

We are a company that owns 2 compliance software programs for TV, Radio and Cable industries as well as an online job board. We need a professional business card that incorproates all three logos.

```html
<!DOCTYPE html>
<html lang="en">
<head>
<meta charset="utf-8">
<title>Clear Harbor Business Card</title>
<link href="https://fonts.googleapis.com/css2?family=Montserrat:wght@400;600;700&family=Oswald:wght@500;600&display=swap" rel="stylesheet">
<style>
  :root {
    --page-bg: #141517;
    --card-bg: #1f2124;
    --purple: #2e2a7c;
    --red: #e8432a;
    --blue: #2f8fe0;
    --grey: #9aa0a6;
    --white: #f4f4f4;
  }
  * { box-sizing: border-box; margin: 0; padding: 0; }
  html, body { width: 1200px; height: 800px; overflow: hidden; background: var(--page-bg); }
  body {
    display: flex; align-items: center; justify-content: center; gap: 40px;
    font-family: "Montserrat", sans-serif;
  }
  .card {
    position: relative; width: 540px; height: 308px; flex: none;
    background: var(--card-bg); border-radius: 14px; overflow: hidden;
    box-shadow: 0 18px 40px rgba(0,0,0,.55);
  }
  .brand-row {
    position: absolute; left: 20px; right: 20px;
    display: flex; flex-wrap: nowrap; align-items: center; justify-content: center;
  }
  .card--front .brand-row { top: 50%; transform: translateY(-50%); }
  .card--back .brand-row { top: 52px; }
  .brand { display: flex; flex-direction: column; align-items: flex-start; padding: 2px 14px; flex: none; }
  .brand + .brand { border-left: 1px solid var(--purple); }
  .brand__name { font-weight: 700; font-size: 14px; line-height: 1.15; white-space: nowrap; }
  .brand__tag { font-size: 6.5px; letter-spacing: .08em; color: var(--grey); margin-top: 4px; text-transform: uppercase; white-space: nowrap; }
  .brand--broadcast .brand__name,
  .brand--cable .brand__name { color: var(--red); }
  .brand--jobs { flex-direction: row; align-items: center; gap: 7px; }
  .brand--jobs .brand__name { color: var(--blue); }
  .brand__dot { width: 16px; height: 16px; border-radius: 50%; background: var(--blue); flex: none; }

  .person { position: absolute; left: 52px; top: 170px; width: 200px; }
  .person__name { font-family: "Oswald", sans-serif; font-weight: 600; font-size: 28px; color: var(--white); letter-spacing: .02em; text-transform: uppercase; white-space: nowrap; }
  .person__title { font-size: 14px; color: var(--red); margin-top: 2px; }
  .divider { position: absolute; left: 262px; top: 166px; width: 1px; height: 76px; background: var(--purple); }
  .contact { position: absolute; left: 284px; top: 168px; list-style: none; }
  .contact li { display: flex; align-items: center; gap: 9px; font-size: 12.5px; color: var(--white); line-height: 24px; white-space: nowrap; }
  .contact svg { width: 12px; height: 12px; flex: none; }

  .edge-band { position: absolute; left: 0; right: 0; bottom: 0; height: 7px; display: flex; }
  .edge-band__purple { width: 42%; background: var(--purple); }
  .edge-band__red { flex: 1; background: var(--red); }
</style>
</head>
<body>
  <section class="card card--front">
    <div class="brand-row">
      <div class="brand brand--broadcast">
        <span class="brand__name">Harbor Broadcast</span>
        <span class="brand__tag">Broadcast Compliance</span>
      </div>
      <div class="brand brand--cable">
        <span class="brand__name">Harbor Cable</span>
        <span class="brand__tag">MVPD Compliance</span>
      </div>
      <div class="brand brand--jobs">
        <span class="brand__dot"></span>
        <span class="brand__name">StageRoster.com</span>
      </div>
    </div>
  </section>

  <section class="card card--back">
    <div class="brand-row">
      <div class="brand brand--broadcast">
        <span class="brand__name">Harbor Broadcast</span>
        <span class="brand__tag">Broadcast Compliance</span>
      </div>
      <div class="brand brand--cable">
        <span class="brand__name">Harbor Cable</span>
        <span class="brand__tag">MVPD Compliance</span>
      </div>
      <div class="brand brand--jobs">
        <span class="brand__dot"></span>
        <span class="brand__name">StageRoster.com</span>
      </div>
    </div>

    <div class="person">
      <p class="person__name">Alex Moreno</p>
      <p class="person__title">Director</p>
    </div>
    <div class="divider"></div>
    <ul class="contact">
      <li>
        <svg viewBox="0 0 12 12" aria-hidden="true"><rect x="1" y="1" width="10" height="10" fill="none" stroke="#e8432a" stroke-width="1.6"/></svg>
        (123) 456 7890
      </li>
      <li>
        <svg viewBox="0 0 12 12" aria-hidden="true"><rect x="0.5" y="2" width="11" height="8" fill="#e8432a"/><path d="M0.5 2 L6 7 L11.5 2" fill="none" stroke="#1f2124" stroke-width="1"/></svg>
        info@clearharbor.com
      </li>
      <li>
        <svg viewBox="0 0 12 12" aria-hidden="true"><circle cx="6" cy="6" r="5" fill="#e8432a"/><path d="M1 6 H11 M6 1 V11 M2.5 3.5 H9.5 M2.5 8.5 H9.5" stroke="#1f2124" stroke-width=".8"/></svg>
        www.clearharbor.com
      </li>
    </ul>

    <div class="edge-band">
      <span class="edge-band__purple"></span>
      <span class="edge-band__red"></span>
    </div>
  </section>
</body>
</html>
```